Fresh, modern, fun business card for pediatric dental practice

Need a business card for fresh, modern, fun pediatric dental practice

Clean look that matches our website's font and colors

We prefer the look of curved corners on business cards

Target Market(s)

parents (mothers) of young children, professionals, mid-high class

Industry/Entity Type

Dental

Contact Information for Business Card

Maplebrook Pediatric Dentistry
482 Quarry Lane
Suite 517
Cedarton, PA 17590
717.555.0193
www.maplebrookkidsdental.example

Mei-Ran Tsai, DMD
Corinne Walbeck, DMD
(we are working on our email address, but we would like that on the card as well)

Font styles to use
Sans Serif

Requirements
Must have
• All info; we would also like to make cards for individual staff members
• colors from our website and color palatte, attatched
• use same font and design as website for branding
Nice to have
• clean, simple card that has a pop of color
• we would like to see a few designs with our tag line "where smiles get brighter"
• we are not sure if we want to have it on there or not
• we would like to see a few designs incorporating the ribbon graphic on our website where the word WELCOME is

```html
<!DOCTYPE html>
<html lang="en">
<head>
<meta charset="utf-8">
<title>Maplebrook Pediatric Dentistry — Business Card</title>
<link rel="stylesheet" href="https://fonts.googleapis.com/css2?family=Lato:wght@400;700&display=swap">
<style>
  :root {
    --backdrop: #141414;
    --card: #262626;
    --card-edge: #303030;
    --sun: #f2b31f;
    --berry: #d2368f;
    --ink: #f2f2f2;
    --emboss: #5c5c5c;
  }
  * { box-sizing: border-box; margin: 0; padding: 0; }
  html, body { width: 1200px; height: 897px; overflow: hidden; }
  body {
    background: var(--backdrop);
    font-family: "Lato", sans-serif;
    color: var(--ink);
    position: relative;
  }
  .card {
    position: absolute;
    left: 304px;
    width: 594px;
    height: 338px;
    border-radius: 22px;
    background: linear-gradient(135deg, #202020 0%, var(--card) 55%, var(--card-edge) 100%);
  }
  .card--front { top: 92px; }
  .card--back { top: 470px; }

  .brand {
    position: absolute;
    text-align: center;
    font-weight: 700;
    line-height: 1;
  }
  .brand__mark {
    display: block;
    width: 26px; height: 26px;
    border-radius: 50%;
    margin: 0 auto 12px;
  }
  .brand__name { display: block; font-size: 36px; letter-spacing: 0.5px; }
  .brand__tag { display: block; font-size: 17px; letter-spacing: 1.6px; margin-top: 6px; }

  .card--front .brand { left: 62px; top: 62px; width: 220px; color: var(--sun); }
  .card--front .brand__mark { background: var(--sun); }

  .divider {
    position: absolute;
    left: 295px; top: 100px;
    width: 2px; height: 116px;
    background: var(--berry);
  }
  .person { position: absolute; left: 324px; top: 98px; }
  .person__name { color: var(--sun); font-size: 19.5px; letter-spacing: 0.8px; font-weight: 400; }
  .person__title { font-size: 15px; margin-top: 5px; }
  .contact { list-style: none; margin-top: 22px; }
  .contact__item {
    display: flex; align-items: center;
    font-size: 13.5px; height: 19.2px;
    letter-spacing: 0.2px;
  }
  .contact__icon { width: 11px; height: 11px; margin: 0 12px 0 6px; flex: none; }

  .practice {
    position: absolute; left: 0; right: 0; top: 277px;
    text-align: center;
  }
  .practice__name { color: var(--sun); font-size: 14.5px; letter-spacing: 0.3px; }
  .practice__address { font-size: 15px; margin-top: 4px; letter-spacing: 0.2px; }

  .card--back .brand { left: 0; right: 0; top: 86px; color: var(--emboss); }
  .card--back .brand__mark { background: var(--emboss); width: 40px; height: 40px; margin-bottom: 16px; }
  .card--back .brand__name { font-size: 50px; letter-spacing: 1px; }
  .card--back .brand__tag { font-size: 24px; letter-spacing: 2.6px; margin-top: 8px; }

  .web {
    position: absolute; left: 0; right: 0; top: 291px;
    text-align: center; font-size: 16px; letter-spacing: 1.8px;
  }
  .web__domain { color: var(--sun); }
</style>
</head>
<body>
  <section class="card card--front">
    <div class="brand">
      <span class="brand__mark"></span>
      <span class="brand__name">maplebrook</span>
      <span class="brand__tag">pediatric dentistry</span>
    </div>
    <div class="divider"></div>
    <div class="person">
      <h1 class="person__name">CORINNE WALBECK</h1>
      <p class="person__title">DMD</p>
      <ul class="contact">
        <li class="contact__item">
          <svg class="contact__icon" viewBox="0 0 24 24" fill="#f2b31f"><path d="M6.6 10.8a15.1 15.1 0 0 0 6.6 6.6l2.2-2.2c.3-.3.7-.4 1-.2 1.1.4 2.3.6 3.6.6.6 0 1 .4 1 1V20c0 .6-.4 1-1 1A17 17 0 0 1 3 4c0-.6.4-1 1-1h3.5c.6 0 1 .4 1 1 0 1.3.2 2.5.6 3.6.1.3 0 .7-.2 1z"/></svg>
          717.555.0193
        </li>
        <li class="contact__item">
          <svg class="contact__icon" viewBox="0 0 24 24"><rect x="2" y="5" width="20" height="14" fill="#f2b31f"/><path d="M2 5l10 8 10-8" fill="none" stroke="#262626" stroke-width="2"/></svg>
          info@maplebrookkidsdental.example
        </li>
        <li class="contact__item">
          <svg class="contact__icon" viewBox="0 0 24 24" fill="none" stroke="#f2b31f" stroke-width="2"><circle cx="12" cy="12" r="10"/><path d="M2 12h20M12 2c3 3 3 17 0 20M12 2c-3 3-3 17 0 20"/></svg>
          www.maplebrookkidsdental.example
        </li>
      </ul>
    </div>
    <div class="practice">
      <p class="practice__name">MAPLEBROOK PEDIATRIC DENTISTRY</p>
      <p class="practice__address">482 Quarry Lane Suite 517 Cedarton, PA 17590</p>
    </div>
  </section>

  <section class="card card--back">
    <div class="brand">
      <span class="brand__mark"></span>
      <span class="brand__name">maplebrook</span>
      <span class="brand__tag">pediatric dentistry</span>
    </div>
    <p class="web">www.<span class="web__domain">maplebrookkidsdental</span>.example</p>
  </section>
</body>
</html>
```